Aquatic View

We need a web design for a new window cleaning company name Tidewell Glass Care. We are located in Grand Cayman, Cayman Islands. We are a small company, a team of husband and wife. Our services include residencial interior and exterior window cleaning and commercial. Extra services such as ceiling fans cleaning, mirrors, high dusting. Home cleaning services. Power washing. Explaining the service. We want a modern, beachy style with aquatic colors. We want to use our domain name "tidewellglasscare.ky". We want to portray a clean, modern and professional design.

Target Market(s)

Big Home owners

Industry/Entity Type

Cleaning Service

Contact Information for Business Card

Company Name: Tidewell Glass Care
Name: Desmond Farrowby owner/manager
Phone: 345-9170452
Email: desmond@tidewellglasscare.ky
Website: tidewellglasscare.ky
Address: P.O.Box 2486 GT, George Town, Grand Cayman KY1-1203 Cayman Islands

Number of Pages Required

2 page

Font styles to use
Sans Serif

Colors
0592cd
0455a3
33a6d7
85cae6
cadf82
abd036
fbf289

Requirements
Nice to have
• Pictures of an ocean view and palm trees from clear windows.
• https://quorvantel.com/bidlinker/
• Use the above for "free estimate".

```html
<!DOCTYPE html>
<html lang="en">
<head>
<meta charset="utf-8">
<title>Tidewell Glass Care</title>
<link rel="stylesheet" href="https://fonts.googleapis.com/css2?family=Play:wght@400;700&family=Roboto:wght@400;500&display=swap">
<style>
:root{
  --blue:#0f6fb5;
  --blue-dark:#0d5a98;
  --blue-band-top:#1e7cc2;
  --blue-band-bot:#125c9c;
  --cyan:#a6f3f7;
  --cyan-line:#9ee8f2;
  --ink:#222;
  --grey-text:#7a7a7a;
  --title-grey:#666;
  --soft-bg:#f5f5f5;
  --footer-bg:#363636;
  --footer-text:#cfcfcf;
  --white:#fff;
}
*{box-sizing:border-box;margin:0;padding:0}
html,body{width:1172px;height:1200px;overflow:hidden;background:var(--white)}
body{font-family:"Roboto",sans-serif;color:var(--ink);position:relative}
.display{font-family:"Play",sans-serif}

.site-header{position:absolute;top:0;left:0;width:1172px;height:86px}
.brand{position:absolute;left:129px;top:30px;display:flex;align-items:center;gap:7px;font-family:"Play",sans-serif;font-weight:700;font-size:13px;color:var(--blue-dark);letter-spacing:.3px}
.brand .mark{width:14px;height:14px;border-radius:50%;background:var(--blue)}
.main-nav{position:absolute;right:131px;top:33px;display:flex;gap:31px;font-family:"Play",sans-serif;font-size:13.5px;color:#333}
.main-nav .active{color:var(--blue)}
.header-rule{position:absolute;top:86px;left:0;width:1172px;height:4px;background:var(--cyan-line)}

.hero{position:absolute;top:90px;left:0;width:1172px;height:355px;overflow:hidden}
.hero-scene{position:absolute;inset:0;background:linear-gradient(180deg,#4db3ea 0%,#a7d8f3 40%,#d9eef8 48%,#2cc3d6 55%,#86dde4 75%,#eef2ef 100%)}
.call-box{position:absolute;top:-1px;left:815px;width:228px;height:40px;background:var(--cyan);display:flex;align-items:center;gap:8px;padding-left:13px;font-family:"Play",sans-serif;font-size:15.5px;color:var(--blue-dark)}
.hero-title{position:absolute;left:129px;top:264px;font-family:"Play",sans-serif;font-size:26px;color:#666;letter-spacing:.2px}
.hero-dots{position:absolute;top:323px;left:546px;display:flex;gap:16px}
.hero-dots span{width:8px;height:8px;border-radius:50%;background:#3a3a3a}
.hero-dots span.on{background:var(--blue)}

.services{position:absolute;top:445px;left:0;width:1172px;height:154px;background:linear-gradient(180deg,var(--blue-band-top),var(--blue-band-bot));display:flex}
.service{position:relative;display:flex;flex-direction:column;align-items:center;padding-top:26px;color:var(--white)}
.service+.service{border-left:1px solid rgba(255,255,255,.12)}
.service svg{height:72px}
.service h3{margin-top:11px;font-family:"Play",sans-serif;font-weight:400;font-size:19px}

.welcome{position:absolute;top:599px;left:0;width:1172px;height:293px}
.team-photo{position:absolute;left:129px;top:46px;width:376px;height:247px;background:radial-gradient(ellipse at 50% 60%,#d9e6f2 0%,#f3f6f9 60%,#fff 100%)}
.welcome-copy{position:absolute;left:537px;top:61px;width:503px}
.welcome-copy h1{font-family:"Play",sans-serif;font-weight:400;font-size:30px;color:var(--blue);letter-spacing:.2px}
.welcome-copy .lead{margin-top:16px;font-size:13px;line-height:21px;color:#222}
.welcome-copy .body{margin-top:11px;font-size:11px;line-height:20.5px;color:var(--grey-text)}

.testimonials{position:absolute;top:892px;left:0;width:1172px;height:216px;background:var(--soft-bg)}
.testimonials h2{position:absolute;top:24px;width:100%;text-align:center;font-family:"Play",sans-serif;font-weight:400;font-size:21px;color:var(--title-grey)}
.quote-card{position:absolute;left:251px;top:66px;width:670px;height:102px;background:var(--white);border:1px solid #e3e3e3;text-align:center;padding:20px 30px 0}
.quote-card p{font-size:12.5px;line-height:19px;color:#444}
.quote-card cite{display:block;margin-top:9px;font-style:normal;font-size:12.5px;color:var(--blue)}
.quote-dots{position:absolute;top:188px;left:557px;display:flex;gap:10px}
.quote-dots span{width:6px;height:6px;border-radius:50%;background:#e8e8e8;border:1px solid #ccc}
.quote-dots span.on{background:#444;border-color:#444}

.site-footer{position:absolute;top:1108px;left:0;width:1172px;height:92px;background:var(--footer-bg)}
.footer-brand{position:absolute;left:129px;top:21px;width:105px;height:52px;background:#8a8a8a;display:flex;align-items:center;justify-content:center;font-family:"Play",sans-serif;font-weight:700;font-size:11px;color:#2e2e2e}
.footer-nav{position:absolute;left:248px;top:27px;font-size:10.5px;color:var(--footer-text)}
.footer-nav span{margin:0 6px;color:#aaa}
.copyright{position:absolute;left:248px;top:54px;font-size:10.5px;color:var(--footer-text)}
.social{position:absolute;left:1016px;top:33px;width:26px;height:26px;border-radius:50%;background:#3b5aa8}
</style>
</head>
<body>

<header class="site-header">
  <div class="brand"><span class="mark"></span>Tidewell Glass Care</div>
  <nav class="main-nav">
    <span class="active">Home</span><span>About us</span><span>Services</span><span>Testimonials</span><span>Contact us</span>
  </nav>
</header>
<div class="header-rule"></div>

<section class="hero">
  <div class="hero-scene" role="img" aria-label="Ocean view with a palm tree seen through clear paned windows"></div>
  <div class="call-box">
    <svg width="13" height="13" viewBox="0 0 24 24"><path fill="#0d5a98" d="M6.6 10.8c1.4 2.8 3.8 5.1 6.6 6.6l2.2-2.2c.3-.3.7-.4 1-.2 1.1.4 2.3.6 3.6.6.6 0 1 .4 1 1V20c0 .6-.4 1-1 1C10.6 21 3 13.4 3 4c0-.6.4-1 1-1h3.5c.6 0 1 .4 1 1 0 1.3.2 2.5.6 3.6.1.3 0 .7-.2 1z"/></svg>
    Call us on : 564 318 2907
  </div>
  <div class="hero-title">Tidewell Glass Care in Cayman Islands</div>
  <div class="hero-dots"><span class="on"></span><span></span><span></span><span></span></div>
</section>

<section class="services">
  <div class="service" style="width:345px">
    <svg viewBox="0 0 96 72" width="96"><g fill="none" stroke="#fff" stroke-width="1.5"><rect x="1" y="1" width="94" height="70"/><line x1="48" y1="1" x2="48" y2="71"/><line x1="1" y1="36" x2="95" y2="36"/><rect x="7" y="7" width="35" height="23"/><rect x="54" y="7" width="35" height="23"/><rect x="7" y="42" width="35" height="23"/><rect x="54" y="42" width="35" height="23"/></g></svg>
    <h3>Windows Cleaning</h3>
  </div>
  <div class="service" style="width:275px">
    <svg viewBox="0 0 74 74" width="74"><g fill="none" stroke="#fff" stroke-width="1.5"><circle cx="37" cy="37" r="35"/><circle cx="37" cy="37" r="5"/><path d="M37 32 C30 22 34 12 44 14 C52 16 46 28 41 33"/><path d="M42 38 C54 38 60 46 54 54 C48 60 42 50 40 42"/><path d="M33 40 C26 50 16 52 14 44 C12 36 24 36 32 36"/></g></svg>
    <h3>Ceiling Fans Cleaning</h3>
  </div>
  <div class="service" style="width:250px">
    <svg viewBox="0 0 56 72" width="56"><g fill="none" stroke="#fff" stroke-width="1.5"><rect x="1" y="1" width="54" height="70"/><rect x="9" y="11" width="38" height="44"/><path d="M9 50 L22 32 L32 42 L38 36 L47 46"/><circle cx="36" cy="22" r="3"/></g></svg>
    <h3>Mirrors Cleaning</h3>
  </div>
  <div class="service" style="width:302px">
    <svg viewBox="0 0 76 72" width="76"><g fill="none" stroke="#fff" stroke-width="1.5"><rect x="2" y="1" width="48" height="68" rx="3"/><line x1="2" y1="18" x2="50" y2="18"/><circle cx="42" cy="10" r="3"/><circle cx="16" cy="54" r="12"/><circle cx="16" cy="54" r="7"/><path d="M50 12 H62 Q68 12 68 20 V40"/><rect x="62" y="40" width="12" height="6"/></g></svg>
    <h3>High Dusting</h3>
  </div>
</section>

<section class="welcome">
  <div class="team-photo" role="img" aria-label="Husband and wife cleaning team holding brooms and cleaning supplies"></div>
  <div class="welcome-copy">
    <h1>Welcome to Tidewell Glass Care</h1>
    <p class="lead">Nullam accumsan purus vel tempus viverra. Mauris suscipit felis id nunc elementum varius. Praesent elementum nulla sit amet justo pellentesque scelerisque.</p>
    <p class="body">Nam et tortor in ante iaculis porttitor in luctus mi. Vivamus gravida sem a pretium euismod. Nam lobortis, purus et fringilla tempus, risus eros dignissim diam, eget finibus sem risus sit amet eros. Vestibulum facilisis dolor at purus tincidunt porta. Nam fringilla nulla vel nisl condimentum, dapibus condimentum enim porta. Phasellus blandit quam a ipsum gravida dapibus.</p>
  </div>
</section>

<section class="testimonials">
  <h2>TESTIMONIALS</h2>
  <blockquote class="quote-card">
    <p>“ &nbsp;Praesent elementum nulla sit amet justo pellentesque scelerisque. Nam et tortor in ante iaculis porttitor in luctus mi. Vivamus gravida sem a pretium euismod. &nbsp;”</p>
    <cite>Marla Quint, NY</cite>
  </blockquote>
  <div class="quote-dots"><span class="on"></span><span></span><span></span><span></span></div>
</section>

<footer class="site-footer">
  <div class="footer-brand">Tidewell Glass Care</div>
  <div class="footer-nav">Home<span>|</span>About us<span>|</span>Services<span>|</span>Testimonials<span>|</span>Contact us</div>
  <div class="copyright">Copyright &nbsp;© 2015 &nbsp;Tidewell Glass Care. &nbsp; All rights reserved.</div>
  <div class="social" aria-label="Social link"></div>
</footer>

</body>
</html>
```